new signage design for budget motel - Brookfern Lodge

renaming the budget motel as Brookfern Lodge, property located on side of a hill. therefore i choose to name is Brookfern Lodge, im looking for clean, modern look in signage design,this property does not have a Logo, plan to us signage design as a logo as well. current pole sign housing is rectangle shape and will be using same housing I'll be attaching picture of the signage for better idea. looking forward to awesome creative designs.

Industry/Entity Type

Motel

Font styles to use
Serif
Sans Serif

Requirements
Should not have
• mountains , mountain(s) with snow , trees, no black color, red color, blue letters, too much green.

```html
<!DOCTYPE html>
<html lang="en">
<head>
<meta charset="utf-8">
<title>Brookfern Lodge – Pole Sign</title>
<link rel="stylesheet" href="https://fonts.googleapis.com/css2?family=Permanent+Marker&display=swap">
<style>
  :root {
    --backdrop: #f0f0f0;
    --sign-white: #ffffff;
    --lodge-brown: #3a1507;
    --sun-yellow: #ffcc00;
    --sign-shadow: rgba(0, 0, 0, 0.22);
  }
  * { margin: 0; padding: 0; box-sizing: border-box; }
  html, body {
    width: 800px;
    height: 1200px;
    overflow: hidden;
    background: var(--backdrop);
  }
  .canvas {
    position: relative;
    width: 800px;
    height: 1200px;
    display: flex;
    align-items: center;
    justify-content: center;
  }
  .sign-face {
    width: 720px;
    height: 540px;
    background: var(--sign-white);
    box-shadow: 0 2px 10px var(--sign-shadow);
  }
  .sign-face svg { display: block; width: 100%; height: 100%; }
  .brand-word {
    font-family: "Permanent Marker", "Comic Sans MS", cursive;
    text-anchor: middle;
  }
  .brand-word--name { fill: var(--lodge-brown); }
  .brand-word--type { fill: var(--sign-white); }
  .hill-band { fill: var(--lodge-brown); }
  .sun-stripe { fill: var(--sun-yellow); }
</style>
</head>
<body>
  <main class="canvas">
    <section class="sign-face" aria-label="Brookfern Lodge sign">
      <svg viewBox="0 0 1296 972" xmlns="http://www.w3.org/2000/svg">
        <path class="hill-band" d="M0,542 C400,498 900,530 1296,812 L1296,972 L0,972 Z"/>
        <path class="sun-stripe" d="M0,574 C420,520 900,555 1278,798 C900,582 420,552 0,610 Z"/>
        <text class="brand-word brand-word--name" x="650" y="400" font-size="215" textLength="1130" lengthAdjust="spacingAndGlyphs">BROOKFERN</text>
        <text class="brand-word brand-word--type" x="640" y="858" font-size="200" textLength="520" lengthAdjust="spacingAndGlyphs">LODGE</text>
      </svg>
    </section>
  </main>
</body>
</html>
```